Tall Fern Roofing Business Card

Need a business card with the logo that was designed here

Contact Information for Business Card

Name, Title, Phone, Email, Website, Company name

```html
<!DOCTYPE html>
<html lang="en">
<head>
<meta charset="utf-8">
<title>Tall Fern Roofing – Business Card</title>
<link href="https://fonts.googleapis.com/css2?family=Open+Sans:wght@400;600;700&display=swap" rel="stylesheet">
<style>
  :root{
    --backdrop:#323232;
    --brand-blue:#1676c2;
    --roof-grey:#939598;
    --card-white:#ffffff;
    --ink:#1c1c1c;
    --back-grey-dark:#86878b;
    --back-grey-light:#a9aaad;
  }
  *{margin:0;padding:0;box-sizing:border-box}
  html,body{width:1200px;height:780px;overflow:hidden;background:var(--backdrop)}
  body{position:relative;font-family:"Open Sans",Arial,sans-serif}

  .card{position:absolute;width:560px;height:320px;overflow:hidden;box-shadow:0 10px 24px rgba(0,0,0,.45)}

  /* Back side */
  .card-back{left:40px;top:60px;background:var(--back-grey-dark)}
  .back-pattern{position:absolute;inset:0;background:linear-gradient(135deg,var(--back-grey-light) 0%,var(--back-grey-dark) 55%,#7d7e82 100%)}
  .back-brand{position:absolute;left:300px;top:140px;display:flex;align-items:center;gap:10px;
    color:#fff;font-weight:700;font-size:22px;letter-spacing:.5px}
  .brand-square{width:14px;height:14px;background:currentColor}

  /* Front side */
  .card-front{left:600px;top:400px;background:var(--card-white)}
  .front-brand{position:absolute;left:40px;top:108px;display:flex;align-items:center;gap:10px;
    color:var(--brand-blue);font-weight:700;font-size:27px;letter-spacing:.3px}

  .name-block{position:absolute;right:38px;top:18px;text-align:right}
  .person-name{font-size:32px;font-weight:700;line-height:1.05;letter-spacing:.5px}
  .person-name .first{color:var(--brand-blue)}
  .person-name .last{color:var(--roof-grey)}
  .person-title{font-size:15px;font-weight:600;color:var(--ink);margin-top:2px}
  .name-bar{position:absolute;right:0;top:10px;width:18px;height:64px;background:var(--brand-blue)}

  .front-art{position:absolute;inset:0}

  .contact{position:absolute;left:30px;top:192px;color:#fff;font-size:14px;line-height:18px}
  .contact .address{margin-bottom:4px}
  .contact ul{margin:0}
  .contact li{list-style:none;display:flex;align-items:center;gap:8px}
  .contact svg{width:13px;height:13px;flex:none}
</style>
</head>
<body>

<section class="card card-back" aria-label="Business card back">
  <div class="back-pattern" role="img" aria-label="Repeating pattern of small house roofs in tonal greys"></div>
  <div class="back-brand"><span class="brand-square"></span>Tall Fern Roofing</div>
</section>

<section class="card card-front" aria-label="Business card front">
  <svg class="front-art" viewBox="0 0 560 320" width="560" height="320">
    <polygon class="contact-band" points="0,185 328,185 264,296 0,296" fill="var(--brand-blue)"/>
    <polygon class="base-band" points="0,302 261,302 251,320 0,320" fill="var(--brand-blue)"/>
    <defs>
      <linearGradient id="roofTone" x1="0" y1="0" x2="1" y2="0">
        <stop offset="0" stop-color="#3a88c9"/>
        <stop offset="1" stop-color="#a3a5a8"/>
      </linearGradient>
    </defs>
    <polygon role="img" aria-label="Large house roof and window graphic in brand blue and grey"
      points="272,320 340,150 470,118 560,200 560,320" fill="url(#roofTone)" opacity=".85"/>
  </svg>

  <div class="front-brand"><span class="brand-square"></span>Tall Fern Roofing</div>

  <div class="name-bar"></div>
  <div class="name-block">
    <div class="person-name"><span class="first">Dale</span> <span class="last">Marsh</span></div>
    <div class="person-title">Managing Director</div>
  </div>

  <div class="contact">
    <p class="address">418 Cedar Hollow Rd. Suite 120<br>Greenvale, TX 75014</p>
    <ul>
      <li><svg viewBox="0 0 24 24"><path fill="#fff" d="M6.6 10.8a15 15 0 0 0 6.6 6.6l2.2-2.2c.3-.3.7-.4 1-.2 1.1.4 2.3.6 3.6.6.6 0 1 .4 1 1V20c0 .6-.4 1-1 1A17 17 0 0 1 3 4c0-.6.4-1 1-1h3.5c.6 0 1 .4 1 1 0 1.3.2 2.5.6 3.6.1.3 0 .7-.2 1z"/></svg>(555) 204-1187</li>
      <li><svg viewBox="0 0 24 24"><path fill="#fff" d="M3 5h18v14H3zM4.5 6.5v.4L12 12l7.5-5.1v-.4z"/></svg>info@website.com</li>
      <li><svg viewBox="0 0 24 24"><circle cx="12" cy="12" r="9" fill="none" stroke="#fff" stroke-width="2"/><path d="M3 12h18M12 3c3 3 3 15 0 18M12 3c-3 3-3 15 0 18" fill="none" stroke="#fff" stroke-width="1.5"/></svg>www.website.com</li>
    </ul>
  </div>
</section>

</body>
</html>
```